TLMWOS - Website Design

We require a WordPress website for an accounting firm.
Please review our concept design found on our development site:
http://quillmarsh.ca/tlmwoxe.
The client would like to carry the look and feel of the National Corporate site http://www.tlm.ca as well.
The site must be mobile ready (responsive)
The client will be providing a collection of staff photos for a contact page
Accounting

```html
<!DOCTYPE html>
<html lang="en">
<head>
<meta charset="utf-8">
<title>Wren Otis &amp; Associates — Chartered Professional Accountants</title>
<link href="https://fonts.googleapis.com/css2?family=Open+Sans:ital,wght@0,400;0,600;0,700;1,400&family=Libre+Baskerville&display=swap" rel="stylesheet">
<style>
:root{
  --olive:#8e8f43;
  --olive-dark:#7d7e38;
  --black:#000;
  --ink:#222;
  --body:#666;
  --muted:#888;
  --line:#e2e2e2;
  --footer:#333436;
  --white:#fff;
  --star:#e3a21a;
}
*{box-sizing:border-box;margin:0;padding:0}
html,body{width:1200px;height:2560px;overflow:hidden}
body{position:relative;font-family:"Open Sans",sans-serif;color:var(--body);background:var(--white)}
.abs{position:absolute}

/* header */
.site-header{left:0;top:0;width:1200px;height:100px;background:var(--white);box-shadow:0 2px 6px rgba(0,0,0,.15);z-index:2}
.brand{left:85px;top:28px;display:flex;align-items:center;gap:12px;font-family:"Libre Baskerville",serif;color:var(--olive)}
.brand-mark{width:40px;height:40px;border:2px solid var(--olive)}
.brand-name{font-size:20px;line-height:22px;letter-spacing:.5px}
.brand-sub{font-size:10.5px;letter-spacing:.6px;border-top:1px solid var(--olive);border-bottom:1px solid var(--olive);margin-top:3px;padding:1px 0}
.main-nav{right:85px;top:38px;display:flex;gap:40px;font-size:13.5px;color:var(--ink)}

/* hero scenery */
.scenery{left:0;top:100px;width:1200px;height:2098px;background:linear-gradient(180deg,#7d93b8 0%,#c9cfd8 8%,#f3efe4 16%,#e9dcc8 24%,#a6927f 36%,#7e6d66 50%,#8c6f74 62%,#a47f8a 74%,#7b6a4f 88%,#5b5a3e 100%)}
.hero-title{left:0;top:234px;width:1200px;text-align:center;font-size:42px;color:var(--ink);font-weight:400}
.hero-text{left:200px;top:308px;width:800px;text-align:center;font-size:16px;line-height:31px;color:#8a8a8a}
.hero-arrow{top:302px}

/* feature tiles */
.features{left:85px;top:485px;width:1030px;height:215px;display:flex}
.feature{flex:1;background:var(--olive);color:var(--white);text-align:center;padding:24px 28px 0}
.feature--dark{background:var(--black)}
.feature-icon{width:60px;height:60px;border-radius:50%;background:var(--white);border:3px solid rgba(0,0,0,.35);margin:0 auto 12px;display:flex;align-items:center;justify-content:center}
.feature h3{font-size:21px;font-weight:600;margin-bottom:6px}
.feature p{font-size:10.5px;line-height:21px}

/* content panel */
.panel{left:85px;top:700px;width:1030px;height:1498px;background:var(--white)}
.welcome-title{left:85px;top:732px;width:1030px;text-align:center;font-size:27px;color:var(--black);font-weight:400}
.welcome-text{left:137px;top:780px;width:926px;text-align:center;font-size:11.5px;line-height:26px;color:var(--body)}

.post-photo{left:135px;width:657px;height:298px}
.post-photo--office{top:934px;background:linear-gradient(135deg,#d8e4ee,#9fb3c4 50%,#3d4c5e)}
.post-photo--desk{top:1521px;background:linear-gradient(135deg,#5b6a55,#c9b89a 45%,#e8e3da 70%,#6a7684)}
.post-title{left:135px;width:657px;font-size:15.5px;line-height:26px;color:var(--olive);font-weight:600;text-transform:uppercase}
.post-text{left:135px;width:657px;font-size:11.5px;line-height:26px;color:var(--body)}
.post-meta{left:135px;width:657px;display:flex;align-items:center;gap:22px;font-size:11.5px;color:var(--ink)}
.post-meta span{display:flex;align-items:center;gap:7px}
.stars{margin-left:auto;color:var(--star);letter-spacing:1px;font-size:13px}

.pager{left:571px;top:2110px;display:flex;gap:8px;align-items:center;font-size:12px;color:var(--ink)}
.pager b{width:27px;height:27px;border:1px solid #ccc;display:flex;align-items:center;justify-content:center;font-weight:400}
.pager b.is-current{background:var(--olive);border-color:var(--olive);color:var(--white)}

/* sidebar */
.widget{left:816px;width:261px;border:1px solid var(--line);background:var(--white)}
.widget-head{background:var(--olive);color:var(--white);font-size:15px;font-weight:600;height:50px;line-height:50px;padding-left:12px}
.news-item{margin:0 12px;padding:12px 0 10px;border-bottom:1px solid #ddd}
.news-item:last-child{border-bottom:0}
.news-item h4{font-size:11.5px;line-height:20px;color:var(--ink);font-weight:600}
.news-item p{font-size:10.5px;line-height:21px;color:#777;padding-right:20px}
.news-date{text-align:right;font-size:9.5px;font-style:italic;color:var(--olive)}
.cat-list{list-style:none;padding:12px 0 8px 32px;font-size:12px;color:var(--ink);line-height:30.8px}
.promo{left:816px;width:261px;height:102px;background:var(--olive);color:var(--white);font-weight:600;font-size:15px;line-height:25px;display:flex;align-items:center}

/* footer */
.site-footer{left:0;top:2198px;width:1200px;height:267px;background:var(--footer);color:var(--white)}
.footer-col{top:2234px}
.footer-col h5{font-size:15px;font-weight:600;margin-bottom:18px}
.footer-col p{font-size:12px;line-height:23px}
.tweet{display:flex;gap:16px;font-size:11.5px;line-height:23px;margin-bottom:12px}
.tweet i{width:20px;height:20px;background:var(--white);flex:none;margin-top:4px}
.signup{left:785px;top:2346px;display:flex}
.signup span{width:240px;height:44px;background:var(--white);color:#aaa;font-size:12px;line-height:44px;padding-left:14px}
.signup b{width:90px;height:44px;background:var(--olive);color:var(--white);font-size:15px;font-weight:600;line-height:44px;text-align:center}

.bottom-bar{left:0;top:2465px;width:1200px;height:95px;background:var(--olive);color:var(--white)}
.copyright{left:90px;top:2503px;font-size:11.5px;color:var(--white)}
.social{left:923px;top:2497px;display:flex;gap:20px}
.social i{width:34px;height:34px;display:block}
</style>
</head>
<body>

<header class="site-header abs">
  <div class="brand abs">
    <div class="brand-mark"></div>
    <div>
      <div class="brand-name">WREN OTIS &amp; ASSOCIATES</div>
      <div class="brand-sub">CHARTERED PROFESSIONAL ACCOUNTANTS</div>
    </div>
  </div>
  <nav class="main-nav abs"><span>Home</span><span>About Us</span><span>Portfolio</span><span>Client Services</span><span>Resources</span><span>Contact Us</span></nav>
</header>

<div class="scenery abs" role="img" aria-label="Sunlit mountain valley with a meadow of pink wildflowers"></div>

<h1 class="hero-title abs">How can TLM Help YOU?</h1>
<p class="hero-text abs">Lorem ipsum dolor sit amet, ut at, ligula tristique ut elementum vel wisi enim, vestibulum et nec, turpis cras<br>Lorem ipsum dolor sit amet, ut at, ligula tristique</p>
<svg class="hero-arrow abs" style="left:40px" width="26" height="36" viewBox="0 0 26 36"><path d="M20 4 L6 18 L20 32" fill="none" stroke="#333" stroke-width="6"/></svg>
<svg class="hero-arrow abs" style="left:1132px" width="26" height="36" viewBox="0 0 26 36"><path d="M6 4 L20 18 L6 32" fill="none" stroke="#333" stroke-width="6"/></svg>

<section class="features abs">
  <div class="feature">
    <div class="feature-icon" style="background:#111"><svg width="30" height="26" viewBox="0 0 30 26"><path d="M3 9h6l12-7v22L9 17H3z" fill="#fff"/><path d="M9 17l2 7h4l-2-7" fill="#fff"/><path d="M24 9q3 4 0 8" stroke="#fff" stroke-width="2" fill="none"/></svg></div>
    <h3>Read The Latest News</h3>
    <p>Lorem ipsum dolor sit amet, ut at, ligula tristique ut elementum vel wisi enim, vestibulum et nec, turpis cras Lorem ipsum dolor sit amet, ut at, ligula tristique</p>
  </div>
  <div class="feature feature--dark">
    <div class="feature-icon" style="background:var(--olive);border-color:#fff"><svg width="28" height="28" viewBox="0 0 28 28"><circle cx="14" cy="9" r="6" fill="#fff"/><path d="M3 27q0-11 11-11t11 11z" fill="#fff"/></svg></div>
    <h3>Member</h3>
    <p>Lorem ipsum dolor sit amet, ut at, ligula tristique ut elementum vel wisi enim, vestibulum et nec, turpis cras Lorem ipsum dolor sit amet, ut at, ligula tristique</p>
  </div>
  <div class="feature">
    <div class="feature-icon" style="background:#111"><svg width="28" height="28" viewBox="0 0 28 28"><rect x="3" y="5" width="22" height="20" rx="2" fill="none" stroke="#fff" stroke-width="2.5"/><path d="M3 10h22M9 2v6M19 2v6" stroke="#fff" stroke-width="2.5"/><path d="M9 17l4 4 7-7" stroke="#fff" stroke-width="2.5" fill="none"/></svg></div>
    <h3>JOIN US TODAY</h3>
    <p>Lorem ipsum dolor sit amet, ut at, ligula tristique ut elementum vel wisi enim, vestibulum et nec, turpis cras Lorem ipsum dolor sit amet, ut at, ligula tristique</p>
  </div>
</section>

<div class="panel abs"></div>
<h2 class="welcome-title abs">Welcome To TLM Wren Otis</h2>
<p class="welcome-text abs">Lorem ipsum dolor sit amet, ut at, ligula tristique ut elementum vel wisi enim, vestibulum et nec, turpis cras. Luctus in suspendisse hendrerit aliquam posuere faucibus, et magna eros quam, est egestas donec pellentesque. Condimentum enim. Pellentesque imperdiet nulla lectus sit at. Lorem ipsum dolor sit amet, ut at, ligula tristique ut elementum vel wisi enim, vestibulum et nec, turpis cras. Luctus in suspendisse hendrerit aliquam posuere faucibus, et magna eros quam, est egestas donec pellentesque. Condimentum enim. Pellentesque imperdiet nulla lectus sit at.</p>

<!-- post one -->
<div class="post-photo post-photo--office abs" role="img" aria-label="Business colleagues smiling together at an office meeting table"></div>
<h3 class="post-title abs" style="top:1253px">Hail the selfish employee -harness this selfish motivation for the greater good of your organization</h3>
<p class="post-text abs" style="top:1312px">Lorem ipsum dolor sit amet, ut at, ligula tristique ut elementum vel wisi enim, vestibulum et nec, turpis cras. Luctus in suspendisse hendrerit aliquam posuere faucibus, et magna eros quam, est egestas donec pellentesque. Condimentum enim. Pellentesque imperdiet nulla lectus sit at. Lorem ipsum dolor sit amet, ut at, ligula tristique ut elementum vel wisi enim. vestibulum et nec, turpis cras. Luctus in suspendisse hendrerit aliquam posuere faucibus, et magna eros quam, est egestas donec pellentesque. Condimentum enim. Pellentesque imperdiet nulla lectus sit at.</p>
<div class="post-meta abs" style="top:1460px">
  <span><svg width="14" height="10"><rect width="14" height="10" fill="#777"/><path d="M0 0l7 6 7-6" stroke="#fff" fill="none"/></svg>Email Friends</span>
  <span><svg width="13" height="12"><rect y="4" width="13" height="6" fill="#777"/><rect x="3" width="7" height="4" fill="#777"/></svg>Print</span>
  <span><svg width="14" height="12"><path d="M0 0h14v8H5l-3 4V8H0z" fill="#777"/></svg>Comments</span>
  <span><svg width="12" height="12"><path d="M0 5h3v7H0zM4 5l3-5q2 0 1 4h4v4l-2 4H4z" fill="#777"/></svg>Like</span>
  <span class="stars">★★★★★</span>
</div>

<!-- post two -->
<div class="post-photo post-photo--desk abs" role="img" aria-label="Accountant reviewing paperwork at a desk with calculator and glasses"></div>
<h3 class="post-title abs" style="top:1840px">Hail the selfish employee -harness this selfish motivation for the greater good of your organization</h3>
<p class="post-text abs" style="top:1899px">Lorem ipsum dolor sit amet, ut at, ligula tristique ut elementum vel wisi enim, vestibulum et nec, turpis cras. Luctus in suspendisse hendrerit aliquam posuere faucibus, et magna eros quam, est egestas donec pellentesque. Condimentum enim. Pellentesque imperdiet nulla lectus sit at. Lorem ipsum dolor sit amet, ut at, ligula tristique ut elementum vel wisi enim. vestibulum et nec, turpis cras. Luctus in suspendisse hendrerit aliquam posuere faucibus, et magna eros quam, est egestas donec pellentesque. Condimentum enim. Pellentesque imperdiet nulla lectus sit at.</p>
<div class="post-meta abs" style="top:2047px">
  <span><svg width="14" height="10"><rect width="14" height="10" fill="#777"/><path d="M0 0l7 6 7-6" stroke="#fff" fill="none"/></svg>Email Friends</span>
  <span><svg width="13" height="12"><rect y="4" width="13" height="6" fill="#777"/><rect x="3" width="7" height="4" fill="#777"/></svg>Print</span>
  <span><svg width="14" height="12"><path d="M0 0h14v8H5l-3 4V8H0z" fill="#777"/></svg>Comments</span>
  <span><svg width="12" height="12"><path d="M0 5h3v7H0zM4 5l3-5q2 0 1 4h4v4l-2 4H4z" fill="#777"/></svg>Like</span>
  <span class="stars">★★★★★</span>
</div>

<nav class="pager abs">
  <svg width="14" height="14"><path d="M12 1L2 7l10 6z" fill="#555"/></svg>
  <b class="is-current">1</b><b>2</b><b>3</b><b>4</b><b>5</b>
  <svg width="14" height="14"><path d="M2 1l10 6-10 6z" fill="var(--olive)"/></svg>
</nav>

<!-- sidebar -->
<aside class="widget abs" style="top:932px;height:439px">
  <div class="widget-head">News</div>
  <div class="news-item"><h4>FOREIGN PROPERTIES – REPORT OR NOT REPORT!</h4><p>Canadian residents are taxed on income earned worldwide. In the last few years TRB has been concerned that</p><div class="news-date">- 9days ago</div></div>
  <div class="news-item"><h4>FOREIGN PROPERTIES – REPORT OR NOT REPORT!</h4><p>Canadian residents are taxed on income earned worldwide. In the last few years TRB has been concerned that</p></div>
  <div class="news-item"><h4>FOREIGN PROPERTIES – REPORT OR NOT REPORT!</h4><p>Canadian residents are taxed on income earned worldwide. In the last few years TRB has been concerned that</p></div>
</aside>

<aside class="widget abs" style="top:1410px;height:483px">
  <div class="widget-head">CATEGORIES</div>
  <ul class="cat-list"><li>PAGES</li><li>Categories</li><li>Client Services</li><li>Contact</li><li>Events Calendar</li><li>Financial Tools</li><li>Home</li><li>Info Center</li><li>Locations</li><li>My Bookings</li><li>Profile</li><li>Resources</li><li>Sample Page</li></ul>
</aside>

<div class="promo abs" style="top:1914px;padding-left:12px;justify-content:space-between;padding-right:18px">
  <span>Sign Up to Receive<br>OUR QUARTERLY<br>NEWSLETTER</span>
  <svg width="72" height="68" viewBox="0 0 72 68"><path d="M4 30L36 6l32 24v34H4z" fill="#fff"/><rect x="16" y="16" width="40" height="30" fill="var(--olive)"/><path d="M4 30l32 22 32-22" fill="#fff" stroke="var(--olive)" stroke-width="3"/><path d="M22 24h28M22 31h28" stroke="#fff" stroke-width="3"/></svg>
</div>
<div class="promo abs" style="top:2035px;padding-left:18px;gap:22px">
  <svg width="56" height="56" viewBox="0 0 56 56"><circle cx="28" cy="28" r="25" fill="none" stroke="#fff" stroke-width="3"/><path d="M21 14l5 8-3 4q3 6 8 9l4-3 8 5-3 5q-14 0-21-20z" fill="#fff"/></svg>
  <span>FOR MEMBERS ONLY<br>Member Area login<br>and Discussion Board</span>
</div>

<!-- footer -->
<footer class="site-footer abs"></footer>
<div class="footer-col abs" style="left:85px;width:280px">
  <h5>ABOUT US</h5>
  <p>Lorem ipsum dolor sit amet, consectetur adipisicing elit, sed do eiusmod tempor incididunt ut labore et dolore magna aliqua. Ut enim ad minim veniam, quis nostrud</p>
</div>
<div class="footer-col abs" style="left:435px;width:280px">
  <h5>LATEST TWEET`S</h5>
  <div class="tweet"><i></i><span>Good morning .... wherever you are today! All of us at ...See more here http://lnk.ex/K4pQm7RzT</span></div>
  <div class="tweet"><i></i><span>Good morning .... wherever you are today! All of us at ...See more here http://lnk.ex/K4pQm7RzT</span></div>
</div>
<div class="footer-col abs" style="left:783px;width:310px;top:2240px">
  <h5>NEWSLETTER</h5>
  <p>Excepteur sint occaecat cupidatat non proident, sunt in culpa qui officia deserunt mollit anim</p>
</div>
<div class="signup abs"><span>Enter your email address</span><b>Sign Up</b></div>

<div class="bottom-bar abs"></div>
<p class="copyright abs">© 2014 Company Name &nbsp;All right reserved &nbsp;Term of Use</p>
<div class="social abs">
  <i style="background:#3b5590"></i><i style="background:#2c9ad6"></i><i style="background:#c9c9c9"></i><i style="background:#1b7fb8"></i>
</div>

</body>
</html>
```